Corvane Holdings , new business card design

investment firm with corporate clients . need double sided business card , vertical and horizontal options ,logo must be clear. prefer pantone colors only and sharp design. website also www.corvane.ae

Khalid Bin Tarrafi
Managing Director
Tel. +971 4 387 2940
Mobile +971 50 518 2403
khalid@corvane.ae
Q-Span Plaza, officw 18-B07, Warqa Gardens, Dubai

Contact Information for Business Card

Khalid Bin Tarrafi
Managing Director

Font styles to use
Serif

Colors

Designer to choose colors to be used in the design.

```html
<!DOCTYPE html>
<html lang="en">
<head>
<meta charset="utf-8">
<title>Corvane Holdings – Business Card</title>
<link rel="stylesheet" href="https://fonts.googleapis.com/css2?family=Roboto:wght@300;400&family=Roboto+Condensed:wght@400;700&display=swap">
<style>
  :root {
    --backdrop: #2a2a2c;
    --paper: #f1f1f1;
    --steel-blue: #4e7499;
    --steel-blue-back: #4a7399;
    --ink: #141418;
    --white: #ffffff;
  }
  * { margin: 0; padding: 0; box-sizing: border-box; }
  html, body { width: 1200px; height: 960px; overflow: hidden; }
  body {
    background: var(--backdrop);
    position: relative;
    font-family: "Roboto", Arial, sans-serif;
  }
  .card {
    position: absolute;
    width: 600px;
    height: 343px;
    overflow: hidden;
  }
  .card-front { left: 152px; top: 125px; background: var(--paper); }
  .card-back { left: 452px; top: 500px; background: var(--steel-blue-back); }

  .front-shapes { position: absolute; inset: 0; }

  .brand-name {
    position: absolute;
    font-family: "Roboto", Arial, sans-serif;
    font-weight: 300;
    text-transform: uppercase;
    white-space: nowrap;
    line-height: 1;
  }
  .card-front .brand-name {
    left: 44px; top: 64px;
    font-size: 30px; letter-spacing: 7px;
    color: var(--ink);
  }
  .card-back .brand-name {
    left: 0; right: 0; top: 146px;
    text-align: center;
    font-size: 32px; letter-spacing: 8px;
    color: var(--ink);
  }

  .holder {
    position: absolute;
    right: 35px; top: 188px;
    text-align: right;
    color: var(--white);
    font-family: "Roboto Condensed", Arial, sans-serif;
    line-height: 1;
  }
  .holder-name { font-weight: 700; font-size: 19px; text-transform: uppercase; }
  .holder-title { font-weight: 400; font-size: 15px; margin-top: 5px; text-transform: uppercase; letter-spacing: 0.3px; }

  .address {
    position: absolute;
    left: 44px; top: 208px;
    color: var(--white);
    font-size: 14px; line-height: 18px;
  }
  .contacts {
    position: absolute;
    left: 44px; top: 260px;
    list-style: none;
    color: var(--white);
    font-size: 14px; line-height: 19px;
  }
  .contacts li { display: flex; align-items: center; gap: 6px; }
  .contacts svg { width: 12px; height: 12px; fill: var(--ink); flex: none; }

  .website {
    position: absolute;
    color: var(--white);
    font-size: 14px;
    letter-spacing: 8.5px;
    white-space: nowrap;
  }
  .card-front .website { right: 28px; top: 276px; }
  .card-back .website { left: 0; right: 0; top: 289px; text-align: center; }
</style>
</head>
<body>

<section class="card card-front">
  <svg class="front-shapes" width="600" height="343" viewBox="0 0 600 343">
    <polygon fill="var(--steel-blue)" points="0,173 270,173 281,183 600,183 600,343 0,343"/>
    <polygon fill="var(--ink)" points="281,183 600,183 600,233 336,233"/>
  </svg>

  <div class="brand-name">Corvane Holdings</div>

  <div class="holder">
    <div class="holder-name">Khalid Bin Tarrafi</div>
    <div class="holder-title">Managing Director</div>
  </div>

  <p class="address">Q-Span Plaza, officw 18-B07<br>Warqa Gardens, Dubai</p>

  <ul class="contacts">
    <li>
      <svg viewBox="0 0 12 12"><path d="M2.4 0.6 L4.2 2.8 L3.2 4.2 C3.9 5.7 5.2 7.2 7.8 8.8 L9.2 7.8 L11.4 9.6 L10 11.6 C5 11 1 7 0.4 2 Z"/></svg>
      <span>+971 4 387 2940</span>
    </li>
    <li>
      <svg viewBox="0 0 12 12"><path d="M3 0 H9 V12 H3 Z M4 1.5 V9.5 H8 V1.5 Z"/></svg>
      <span>+971 50 518 2403</span>
    </li>
    <li>
      <svg viewBox="0 0 12 12"><path d="M0 3 H12 V10 H0 Z M1 4 L6 7.3 L11 4 Z" fill-rule="evenodd"/></svg>
      <span>khalid@corvane.ae</span>
    </li>
  </ul>

  <div class="website">www.corvane.ae</div>
</section>

<section class="card card-back">
  <div class="brand-name">Corvane Holdings</div>
  <div class="website">www.corvane.ae</div>
</section>

</body>
</html>
```